Meadow Kr Circle (company name is Meadow Kr Circle LLP)

management of homestay, hospitality something similar with https://www.dorvika.example

Target Market(s)

johor bahru market (Malaysia)

Contact Information for Business Card

Meadow Circle KR LLP

Logo Text

eyes catching, attractive, amazing, Nice, jaw dropping for design

Coding

Coded - Design and coding required

Number of Pages Required

5+ page

Colors

Designer to choose colors to be used in the design.

Requirements
Must have
• please change the short term proposal to our company logo and change the name from dorvika to meadow KR Circle LLP
• thanks
Nice to have
• please let me have eyes catching , jaw dropping design

```html
<!DOCTYPE html>
<html lang="en">
<head>
<meta charset="utf-8">
<title>KR Meadow Circle — Short-stay Management</title>
<link rel="stylesheet" href="https://fonts.googleapis.com/css2?family=Oswald:wght@500;600&family=Poppins:wght@300;400;500&family=Open+Sans:ital,wght@0,400;0,600;1,400&display=swap">
<style>
:root{
  --navy:#1b3f8f;
  --brand:#1d5fb0;
  --ink:#1e1e1e;
  --body:#4a4a4a;
  --green-a:#1f8f7a;
  --green-b:#2fb197;
  --blue-band:#1a4a9c;
  --white:#ffffff;
  --line:#d6d6d6;
  --link:#2a72c4;
}
*{margin:0;padding:0;box-sizing:border-box}
html,body{width:1200px;height:3704px;overflow:hidden;background:var(--white)}
body{position:relative;font-family:"Open Sans",Arial,sans-serif;color:var(--ink)}
.abs{position:absolute}

/* header */
.site-header{position:absolute;left:0;top:0;width:1200px;height:150px;background:var(--white)}
.brand{position:absolute;left:92px;top:48px;display:flex;align-items:center;gap:12px;font-family:"Oswald",sans-serif;font-weight:600;font-size:40px;color:var(--navy);line-height:1}
.brand-mark{width:30px;height:30px;background:var(--brand)}
.main-nav{position:absolute;top:66px;left:520px;display:flex;gap:0;font-family:"Poppins",sans-serif;font-size:18px;color:#333}
.main-nav a{color:inherit;text-decoration:none;margin-right:40px}
.main-nav a.active{color:var(--navy)}

/* hero */
.hero{position:absolute;left:0;top:150px;width:1200px;height:670px}
.hero-photo{position:absolute;inset:0;background:linear-gradient(180deg,#5f7d98 0%,#3d5a78 35%,#2b3f58 70%,#1f2c3f 100%)}
.hero-title{position:absolute;top:183px;width:100%;text-align:center;font-family:"Oswald",sans-serif;font-weight:600;font-size:94px;letter-spacing:2px;color:var(--white);line-height:1}
.hero-sub{position:absolute;top:288px;width:100%;text-align:center;font-family:"Poppins",sans-serif;font-weight:300;font-size:40px;color:var(--white)}
.hero-btn{position:absolute;left:500px;top:375px;width:200px;height:60px;border:2px solid var(--white);color:var(--white);font-family:"Open Sans",sans-serif;font-weight:600;font-size:21px;display:flex;align-items:center;justify-content:center;letter-spacing:.5px}
.hero-edge{position:absolute;left:0;top:540px}

/* about */
.about-box{position:absolute;left:87px;top:912px;width:553px;height:343px;border:2px solid var(--navy);padding:40px 38px}
.section-h{font-family:"Poppins",sans-serif;font-weight:400;color:var(--ink)}
.about-box h2{font-size:46px;line-height:1;margin-bottom:14px}
.about-box p{font-size:15.5px;line-height:26px;color:var(--body);text-align:justify;width:472px}
.about-photo{position:absolute;left:598px;top:965px;width:514px;height:330px;border:2px solid #c9d5e6;background:linear-gradient(135deg,#4e4a3c 0%,#7a6f58 45%,#2e3340 100%)}
.play{position:absolute;left:223px;top:131px}

/* how to start */
.start{position:absolute;left:0;top:1413px;width:1200px;height:496px;background:linear-gradient(90deg,var(--green-a),var(--green-b))}
.notch{position:absolute;left:570px;top:0}
.laptop-photo{position:absolute;left:0;top:77px;width:605px;height:375px;border-radius:0 14px 6px 0;background:linear-gradient(135deg,#6d5a47 0%,#cbb79a 45%,#efe6d6 70%,#8d8f92 100%)}
.start h2{position:absolute;left:595px;top:90px;font-size:44px;color:var(--white)}
.steps{position:absolute;left:595px;top:176px;list-style:none}
.steps::before{content:"";position:absolute;left:19px;top:20px;width:2px;height:162px;background:rgba(255,255,255,.7)}
.steps li{position:relative;display:flex;align-items:center;height:40px;margin-bottom:14px;color:var(--white);font-weight:600;font-size:18px}
.steps .num{width:38px;height:38px;border:2px solid var(--white);border-radius:50%;display:flex;align-items:center;justify-content:center;font-family:"Poppins",sans-serif;font-weight:400;font-size:16px;margin-right:19px;background:var(--green-b)}

/* services */
.services-title{position:absolute;top:2030px;width:100%;text-align:center;font-size:44px}
.service-card{position:absolute;top:2207px;width:315px;height:340px;background:var(--white);border:1px solid var(--line);box-shadow:0 2px 8px rgba(0,0,0,.15);text-align:center;padding:85px 28px 0}
.service-icon{position:absolute;left:94px;top:-62px;width:126px;height:126px;border-radius:50%;background:var(--brand);display:flex;align-items:center;justify-content:center}
.service-card h3{font-family:"Poppins",sans-serif;font-weight:500;font-size:22px;line-height:30px;color:var(--ink);margin-bottom:12px;min-height:60px;display:flex;align-items:center;justify-content:center}
.service-card p{font-size:14.5px;line-height:25px;color:var(--body)}
.read-more{position:absolute;left:0;bottom:30px;width:100%;color:var(--link);font-size:17px}

/* testimonial */
.testimonial{position:absolute;left:0;top:2702px;width:1200px;height:560px}
.testimonial-bg{position:absolute;inset:0;background:linear-gradient(180deg,#1b4b9e 0%,#17428e 60%,#1a4a9c 100%)}
.testimonial h2{position:absolute;top:98px;width:100%;text-align:center;font-size:44px;color:var(--white)}
.quote{position:absolute;left:110px;top:195px;width:980px;text-align:center;color:var(--white);font-size:16.5px;line-height:31px}
.qmark{font-family:Georgia,serif;font-weight:700;font-size:40px;line-height:0;vertical-align:-12px}
.avatar{position:absolute;left:541px;top:302px;width:118px;height:118px;border-radius:50%;border:5px solid var(--white);background:linear-gradient(160deg,#d9c3ad,#8aa6c9)}
.arrow{position:absolute;top:346px}
.client{position:absolute;top:433px;width:100%;text-align:center;color:var(--white);font-style:italic;font-size:17px}

/* footer */
.site-footer{position:absolute;left:0;top:3245px;width:1200px;height:459px;background:linear-gradient(180deg,#ffffff 0%,#f4f6f9 55%,#e9eef5 100%)}
.footer-brand{position:absolute;top:158px;left:0;width:100%;display:flex;justify-content:center;align-items:center;gap:12px;font-family:"Oswald",sans-serif;font-weight:600;font-size:44px;color:var(--navy);line-height:1}
.footer-brand .brand-mark{width:34px;height:34px}
.address{position:absolute;top:263px;width:100%;text-align:center;font-size:16.5px;color:#333;display:flex;justify-content:center;align-items:center;gap:10px}
.social{position:absolute;top:313px;left:473px;display:flex;gap:8px}
.social span{width:44px;height:44px;border:2px solid #222;border-radius:50%}
.copyright{position:absolute;top:384px;width:100%;text-align:center;font-size:13.5px;color:#444}
</style>
</head>
<body>

<header class="site-header">
  <div class="brand"><span class="brand-mark"></span>KR Meadow Circle</div>
  <nav class="main-nav">
    <a class="active" href="#">Home</a><a href="#">About us</a><a href="#">Services</a><a href="#">Project</a><a href="#">Blog</a><a href="#">Contact</a>
  </nav>
</header>

<section class="hero">
  <div class="hero-photo" role="img" aria-label="City skyline of glass office towers at dusk"></div>
  <h1 class="hero-title">KR MEADOW CIRCLE</h1>
  <p class="hero-sub">Short-stay Management Proposal</p>
  <div class="hero-btn">LEARN MORE</div>
  <svg class="hero-edge" width="1200" height="130" viewBox="0 0 1200 130">
    <path d="M0 180 L0 178 L0 170 L0 180Z" fill="#fff"/>
    <path d="M0 175 L0 180Z" fill="#fff"/>
    <path d="M0 180 V180Z" fill="#fff"/>
    <path d="M0 180Z" fill="#fff"/>
    <path d="M0 130 L0 130Z" fill="#fff"/>
    <path d="M0 130 L0 180 Z" fill="#fff"/>
    <path d="M0 60 L60 64 L185 80 L310 78 L430 90 L520 96 L600 135 L680 96 L760 92 L880 84 L1010 70 L1130 60 L1200 48 L1200 130 L0 130Z" fill="#fff"/>
    <path d="M600 135 L520 96 L680 96Z" fill="#23293a"/>
    <g fill="#6a87b0">
      <circle cx="60" cy="64" r="4"/><circle cx="185" cy="80" r="4"/><circle cx="310" cy="78" r="4"/><circle cx="520" cy="96" r="4"/><circle cx="680" cy="96" r="4"/><circle cx="880" cy="84" r="4"/><circle cx="1010" cy="70" r="4"/><circle cx="1160" cy="55" r="4"/>
    </g>
  </svg>
</section>

<section class="about">
  <div class="about-box">
    <h2 class="section-h">About us</h2>
    <p>It is a long established fact that a reader will be distracted by the readable content of a page when looking at its layout. The point of using Lorem Ipsum is that it has a more-or-less normal distribution of letters, as opposed to using 'Content here, content here', making it look like readable English.Many desktop publishing packages and web page editors now use Lorem Ipsum as their default model text, and a search</p>
  </div>
  <div class="about-photo" role="img" aria-label="Business team reviewing a folder in an office">
    <svg class="play" width="66" height="66" viewBox="0 0 66 66"><circle cx="33" cy="33" r="30" fill="rgba(0,0,0,.45)" stroke="#fff" stroke-width="3"/><path d="M26 20 L46 33 L26 46Z" fill="#fff"/></svg>
  </div>
</section>

<section class="start">
  <svg class="notch" width="60" height="20" viewBox="0 0 60 20"><path d="M0 0 H60 L30 18Z" fill="#fff"/><path d="M20 4 L30 12 L40 4" fill="none" stroke="#bbb" stroke-width="2"/></svg>
  <div class="laptop-photo" role="img" aria-label="Laptop showing a furnished living room"></div>
  <h2 class="section-h">How to start?</h2>
  <ol class="steps">
    <li><span class="num">01</span>Getting the required items</li>
    <li><span class="num">02</span>Renovation &amp; Furnishing</li>
    <li><span class="num">03</span>Sign a management agreement</li>
    <li><span class="num">04</span>Handover Keys &amp; Access cards, and relevant information</li>
  </ol>
</section>

<h2 class="section-h services-title">Our Services</h2>

<article class="service-card" style="left:104px">
  <div class="service-icon"><svg width="64" height="40" viewBox="0 0 64 40"><path d="M2 14 L18 4 L32 10 L46 4 L62 14 L56 24 L40 36 L32 30 L24 36 L8 24Z" fill="#fff"/><path d="M22 16 L32 10 L44 22" fill="none" stroke="#1d5fb0" stroke-width="3"/></svg></div>
  <h3>Answering Enquiries, Check-Ins / Outs</h3>
  <p>It is a long established fact that a reader will be distracted by the readable content of a page when looking at its layout. The point of using</p>
  <div class="read-more">Read More »</div>
</article>
<article class="service-card" style="left:447px">
  <div class="service-icon"><svg width="60" height="60" viewBox="0 0 60 60"><path d="M48 6 L30 30" stroke="#fff" stroke-width="5" stroke-linecap="round"/><path d="M22 26 L36 38 L26 52 Q14 54 8 46 Q14 38 22 26Z" fill="none" stroke="#fff" stroke-width="4" stroke-linejoin="round"/></svg></div>
  <h3>Cleaning, Laundry and Maintenance</h3>
  <p>It is a long established fact that a reader will be distracted by the readable content of a page when looking at its layout. The point of using</p>
  <div class="read-more">Read More »</div>
</article>
<article class="service-card" style="left:790px">
  <div class="service-icon"><svg width="60" height="50" viewBox="0 0 60 50"><ellipse cx="24" cy="20" rx="22" ry="16" fill="#fff"/><path d="M10 30 L6 42 L20 34Z" fill="#fff"/><path d="M44 14 Q58 18 56 30 Q54 36 50 38 L54 46 L42 40 Q32 40 28 36" fill="#fff"/></svg></div>
  <h3>Marketing &amp; Optimization</h3>
  <p>It is a long established fact that a reader will be distracted by the readable content of a page when looking at its layout. The point of using</p>
  <div class="read-more">Read More »</div>
</article>

<section class="testimonial">
  <div class="testimonial-bg" role="img" aria-label="Blue-tinted lounge interior backdrop"></div>
  <svg class="abs" style="left:570px;top:0" width="60" height="20" viewBox="0 0 60 20"><path d="M0 0 H60 L30 18Z" fill="#fff"/><path d="M20 4 L30 12 L40 4" fill="none" stroke="#bbb" stroke-width="2"/></svg>
  <h2 class="section-h">Testimonial</h2>
  <p class="quote"><span class="qmark">“</span> It has survived not only five centuries, but also the leap into electronic typesetting, remaining essentially unchanged. It was popularised in the 1960s with the release of Lettrafix sheets containing Lorem Ipsum passages, and more recently with desktop publishing software like Pagewright Studio including versions of Lorem Ipsum <span class="qmark">”</span></p>
  <svg class="arrow" style="left:496px" width="20" height="30" viewBox="0 0 20 30"><path d="M16 2 L4 15 L16 28" fill="none" stroke="#fff" stroke-width="3"/></svg>
  <div class="avatar" role="img" aria-label="Client portrait"></div>
  <svg class="arrow" style="left:684px" width="20" height="30" viewBox="0 0 20 30"><path d="M4 2 L16 15 L4 28" fill="none" stroke="#fff" stroke-width="3"/></svg>
  <p class="client">Neque porro quisquam</p>
  <svg class="abs" style="left:0;top:500px" width="1200" height="60" viewBox="0 0 1200 60"><path d="M0 18 L40 6 L110 22 L200 10 L300 28 L400 12 L480 28 L600 40 L720 26 L800 12 L900 28 L1000 8 L1090 24 L1160 10 L1200 16 V60 H0Z" fill="#fff"/></svg>
</section>

<footer class="site-footer">
  <div class="footer-brand"><span class="brand-mark"></span>KR Meadow Circle</div>
  <p class="address"><svg width="16" height="22" viewBox="0 0 16 22"><path d="M8 0 C3.6 0 0 3.4 0 7.8 C0 13 8 22 8 22 C8 22 16 13 16 7.8 C16 3.4 12.4 0 8 0Z" fill="#1d5fb0"/><circle cx="8" cy="8" r="3" fill="#fff"/></svg>L12-04 Ridgeview Suites, Jalan Seroja, Taman Lestari, 80250 Johor Bahru.</p>
  <div class="social"><span></span><span></span><span></span><span></span><span></span></div>
  <p class="copyright">Copyright © 2018 All Rights Reserved</p>
</footer>

</body>
</html>
```